Kelvaro.ch is looking for business card letterhead and envelope C5 with WOW effect

We need a strong business card for our company Kelvaro.ch, logo is available. You want a black or dark background on which the logo Stark r% 26 # 252; appears. Letterhead and envelope in C5 format should be in a similar design, but does not have to be We need a strong business card for our company Kelvaro.ch, logo is available. A black or dark background is desired, on which the logo Stark comes across. The letterhead and the envelope in C5 format should have a similar design.

Target Market(s)

Private customers as well as entrepreneurs

Contact Information for Business Card

E-mail: info@kelvaro-example.ch
Web.www.Kelvaro-example.ch
Tel: +41 ( 0 ) 79 482 6037
Adresse:
Lindenweg 14
9406 Tarnbach

Hier kann man Icons verwenden für Email,Tel und Adressse

Font styles to use
Other font styles liked:
• Dubai,bold

Colors

Designer to choose colors to be used in the design.

Requirements
Must have
• WOW effect
Nice to have
• R% 26 # 252; back business card with our service listings. - VEHICLE LABELING - SHOP WINDOW LABELING - STICKERS AND MUCH MORE ... in red color

```html
<!DOCTYPE html>
<html lang="en">
<head>
<meta charset="utf-8">
<title>Kelvaro.ch – Business Card</title>
<link rel="stylesheet" href="https://fonts.googleapis.com/css2?family=Open+Sans:wght@400;600;700;800&display=swap">
<style>
  :root {
    --stage: #1b1b1b;
    --card: #232323;
    --card-edge: #2c2c2c;
    --white: #f4f4f4;
    --yellow: #f5c116;
    --red: #e0242b;
  }
  * { margin: 0; padding: 0; box-sizing: border-box; }
  html, body { width: 1200px; height: 900px; overflow: hidden; }
  body {
    background: var(--stage);
    font-family: "Open Sans", Arial, sans-serif;
    color: var(--white);
    position: relative;
  }
  .card {
    position: absolute;
    left: 298px;
    width: 604px;
    height: 390px;
    background: radial-gradient(circle at 75% 40%, #2e2e2e 0%, var(--card) 60%);
    border: 1px solid var(--card-edge);
    box-shadow: 0 14px 30px rgba(0,0,0,0.55);
  }
  .card--front { top: 45px; }
  .card--back { top: 465px; }

  /* Front */
  .brand {
    display: flex;
    align-items: center;
    gap: 14px;
    font-weight: 800;
    font-size: 44px;
    letter-spacing: 1px;
    color: var(--white);
    line-height: 1;
  }
  .brand-dot {
    width: 22px; height: 22px; border-radius: 50%;
    background: var(--yellow);
    flex: none;
  }
  .card--front .brand { position: absolute; left: 150px; top: 138px; }
  .services {
    position: absolute;
    right: 140px;
    top: 226px;
    list-style: none;
    text-align: right;
    font-size: 16px;
    line-height: 22px;
    text-transform: uppercase;
  }
  .services li { display: flex; justify-content: flex-end; align-items: center; gap: 10px; }
  .services li::after {
    content: "";
    width: 8px; height: 8px;
    border: 2px solid var(--red);
    border-radius: 50%;
  }

  /* Back */
  .card--back .brand {
    position: absolute; left: 0; right: 0; top: 52px;
    justify-content: center;
    font-size: 30px;
  }
  .card--back .brand-dot { width: 14px; height: 14px; }
  .person { position: absolute; right: 352px; top: 150px; text-align: right; }
  .person-name { font-weight: 700; font-size: 28px; white-space: nowrap; }
  .person-name .surname { color: var(--yellow); }
  .person-role { font-size: 18px; margin-top: 4px; letter-spacing: 0.5px; }
  .divider {
    position: absolute; left: 276px; top: 150px;
    width: 1px; height: 80px; background: var(--yellow);
  }
  .contacts {
    position: absolute; left: 300px; top: 150px;
    list-style: none; font-size: 18px; line-height: 27px; letter-spacing: 0.5px;
  }
  .contacts li { display: flex; align-items: center; gap: 12px; }
  .contacts svg { width: 15px; height: 15px; flex: none; }
  .address {
    position: absolute; left: 0; right: 0; top: 308px;
    text-align: center; font-size: 19px; letter-spacing: 1px;
  }
</style>
</head>
<body>
  <section class="card card--front" aria-label="Business card front">
    <div class="brand"><span class="brand-dot"></span>KELVARO.CH</div>
    <ul class="services">
      <li>Vehicle labeling</li>
      <li>Shop window labeling</li>
      <li>Stickers and much more</li>
    </ul>
  </section>

  <section class="card card--back" aria-label="Business card back">
    <div class="brand"><span class="brand-dot"></span>KELVARO.CH</div>
    <div class="person">
      <div class="person-name">LUKAS <span class="surname">BRENNER</span></div>
      <div class="person-role">Director</div>
    </div>
    <div class="divider"></div>
    <ul class="contacts">
      <li>
        <svg viewBox="0 0 16 16" aria-hidden="true"><path d="M3 1.5l2.5 0 1 3.5-1.6 1.2c.8 1.8 2.1 3.1 3.9 3.9l1.2-1.6 3.5 1v2.5c0 .8-.7 1.5-1.5 1.5C6.6 13.5 2.5 9.4 2.5 3c0-.8.3-1.5.5-1.5z" fill="var(--yellow)"/></svg>
        +41 ( 0 ) 79 482 6037
      </li>
      <li>
        <svg viewBox="0 0 16 16" aria-hidden="true"><rect x="1.5" y="3.5" width="13" height="9" fill="none" stroke="var(--yellow)" stroke-width="1.5"/><path d="M1.5 3.5L8 9l6.5-5.5" fill="none" stroke="var(--yellow)" stroke-width="1.5"/></svg>
        info@kelvaro-example.ch
      </li>
      <li>
        <svg viewBox="0 0 16 16" aria-hidden="true"><g fill="none" stroke="var(--yellow)" stroke-width="1.3"><circle cx="8" cy="8" r="6.5"/><ellipse cx="8" cy="8" rx="3" ry="6.5"/><path d="M1.5 8h13M2.5 4.8h11M2.5 11.2h11"/></g></svg>
        www.kelvaro-example.ch
      </li>
    </ul>
    <p class="address">Lindenweg 14 9406 Tarnbach</p>
  </section>
</body>
</html>
```